Tolbek cards

I want a simple business card that pops.
Logo on one side.
On side two i want.
"Are you thinking about a new building on your property, or renovating an existing structure? Contact".....
Owners Name: Dale Whitacre
Owners Phone number: 610-555-0187
Address:4076 Copper Ridge RD, Ridgemont, PA 17390
Committed to Quality, Service, and Integrity

```html
<!DOCTYPE html>
<html lang="en">
<head>
<meta charset="utf-8">
<title>Tolbek Builders LLC – Business Card</title>
<link rel="stylesheet" href="https://fonts.googleapis.com/css2?family=Arimo:ital,wght@0,400;0,700;1,700&display=swap">
<style>
  :root {
    --page-bg: #5a5a5a;
    --card-white: #ffffff;
    --brown-dark: #3f2a18;
    --brown-text: #5b3b22;
    --brown-mid: #7a5f45;
    --brown-light: #a08a70;
    --brown-edge: #55381f;
    --grey-text: #555555;
    --divider: #c9c3bd;
  }
  * { margin: 0; padding: 0; box-sizing: border-box; }
  html, body {
    width: 1200px;
    height: 1200px;
    overflow: hidden;
    background: var(--page-bg);
    font-family: "Arimo", Arial, sans-serif;
  }
  .card {
    position: absolute;
    width: 690px;
    height: 394px;
  }
  .card-front {
    left: 266px;
    top: 158px;
    background: var(--card-white);
  }
  .card-back {
    left: 260px;
    top: 652px;
    background: radial-gradient(ellipse 60% 70% at 50% 48%, var(--brown-light) 0%, var(--brown-mid) 50%, var(--brown-edge) 100%);
    display: flex;
    align-items: center;
    justify-content: center;
  }
  .tagline {
    position: absolute;
    left: 0;
    right: 0;
    top: 36px;
    text-align: center;
    font-style: italic;
    font-weight: 700;
    font-size: 17.5px;
    line-height: 24px;
    color: var(--brown-text);
  }
  .brand {
    position: absolute;
    left: 60px;
    width: 260px;
    top: 162px;
    text-align: center;
    color: var(--brown-dark);
    font-weight: 700;
  }
  .brand-name {
    display: block;
    font-size: 44px;
    line-height: 44px;
    letter-spacing: 1px;
  }
  .brand-sub {
    display: block;
    font-size: 14px;
    line-height: 18px;
    letter-spacing: 1.5px;
  }
  .divider {
    position: absolute;
    left: 300px;
    top: 124px;
    width: 1px;
    height: 134px;
    background: var(--divider);
  }
  .contact {
    position: absolute;
    left: 332px;
    top: 133px;
    color: var(--grey-text);
  }
  .contact-name {
    font-size: 25px;
    font-weight: 700;
    color: var(--brown-dark);
    line-height: 30px;
    margin-bottom: 12px;
  }
  .contact-phone {
    display: flex;
    align-items: center;
    gap: 10px;
    font-size: 15.5px;
    margin-bottom: 12px;
  }
  .contact-phone svg { width: 14px; height: 14px; fill: var(--brown-dark); }
  .contact-address {
    font-size: 15.5px;
    line-height: 21px;
    font-style: normal;
  }
  .motto-band {
    position: absolute;
    left: 0;
    right: 0;
    top: 324px;
    height: 35px;
    display: flex;
  }
  .motto-text {
    width: 536px;
    background: var(--brown-dark);
    color: var(--card-white);
    font-size: 16px;
    line-height: 35px;
    padding-left: 98px;
  }
  .motto-square {
    width: 42px;
    margin: 0 1px;
    background: var(--brown-mid);
  }
  .motto-fade {
    flex: 1;
    background: linear-gradient(90deg, var(--brown-mid), var(--brown-light) 45%, var(--brown-mid));
  }
  .back-brand {
    text-align: center;
    color: var(--card-white);
    font-weight: 700;
  }
  .back-brand .brand-name {
    font-size: 78px;
    line-height: 78px;
    letter-spacing: 2px;
  }
  .back-brand .brand-sub {
    font-size: 24px;
    line-height: 34px;
    letter-spacing: 2px;
  }
</style>
</head>
<body>
  <section class="card card-front">
    <p class="tagline">Are you thinking about a new building on your property,<br>or renovating an existing structure?</p>
    <div class="brand">
      <span class="brand-name">TOLBEK</span>
      <span class="brand-sub">BUILDERS LLC</span>
    </div>
    <div class="divider"></div>
    <div class="contact">
      <h1 class="contact-name">DALE WHITACRE</h1>
      <p class="contact-phone">
        <svg viewBox="0 0 24 24" aria-hidden="true"><path d="M6.6 10.8a15.1 15.1 0 0 0 6.6 6.6l2.2-2.2c.3-.3.7-.4 1-.2 1.1.4 2.3.6 3.6.6.6 0 1 .4 1 1V20c0 .6-.4 1-1 1A17 17 0 0 1 3 4c0-.6.4-1 1-1h3.5c.6 0 1 .4 1 1 0 1.3.2 2.5.6 3.6.1.3 0 .7-.2 1z"/></svg>
        610-555-0187
      </p>
      <address class="contact-address">4076 Copper Ridge RD<br>Ridgemont, PA 17390</address>
    </div>
    <div class="motto-band">
      <div class="motto-text">Committed to Quality, Service, and Integrity</div>
      <div class="motto-square"></div>
      <div class="motto-fade"></div>
    </div>
  </section>

  <section class="card card-back">
    <div class="back-brand">
      <span class="brand-name">TOLBEK</span>
      <span class="brand-sub">BUILDERS LLC</span>
    </div>
  </section>
</body>
</html>
```